Real Estate Business Card

On the front side I want to have my info, my brokerage info.
On the back side I want have my complany’s logo, website and Facebook link. I will provide all this once I select a design.

I would like to see Black background and gold text, Dark Blue and gold text and White and blue text designs

Font styles to use
Sans Serif
Script

```html
<!DOCTYPE html>
<html lang="en">
<head>
<meta charset="utf-8">
<title>Stoneway Real Estate – Business Card</title>
<link href="https://fonts.googleapis.com/css2?family=Roboto:wght@400;500;700&display=swap" rel="stylesheet">
<style>
  :root {
    --page: #e6e6e6;
    --card: #1b1c1e;
    --gold: #f0c94a;
    --gold-deep: #d8ac36;
    --text-light: #e4e4e4;
    --divider: #9a9a9a;
  }
  * { margin: 0; padding: 0; box-sizing: border-box; }
  html, body {
    width: 1125px; height: 1200px; overflow: hidden;
    background: var(--page);
    font-family: "Roboto", Arial, sans-serif;
  }
  .card {
    position: absolute;
    left: 150px; width: 826px; height: 472px;
    background: var(--card);
  }
  .card--front { top: 98px; }
  .card--back { top: 630px; }

  /* front */
  .brand {
    position: absolute; left: 40px; width: 380px; top: 190px;
    display: flex; align-items: center; justify-content: center; gap: 14px;
  }
  .brand__mark { width: 26px; height: 26px; background: var(--gold); }
  .brand__name {
    color: var(--gold); font-weight: 700; font-size: 30px;
    letter-spacing: 0.02em; white-space: nowrap;
  }
  .divider {
    position: absolute; left: 454px; top: 88px; width: 2px; height: 300px;
    background: linear-gradient(to bottom, transparent, var(--divider) 20%, var(--divider) 80%, transparent);
  }
  .info { position: absolute; left: 491px; top: 100px; color: var(--text-light); }
  .info__name { color: var(--gold); font-weight: 700; font-size: 29px; line-height: 1.1; }
  .info__title { color: var(--gold-deep); font-weight: 500; font-size: 20px; margin-top: 2px; }
  .info__address { font-size: 19px; line-height: 25px; margin-top: 18px; }
  .contacts { list-style: none; margin-top: 18px; }
  .contacts li {
    display: flex; align-items: center; gap: 12px;
    font-size: 19px; line-height: 26.5px;
  }
  .contacts svg { width: 19px; height: 19px; fill: var(--gold); flex: none; }

  /* back */
  .social-square {
    position: absolute; left: 758px; top: 36px; width: 27px; height: 27px;
    background: var(--gold);
  }
  .back-brand {
    position: absolute; left: 0; right: 0; top: 120px;
    display: flex; flex-direction: column; align-items: center; gap: 26px;
  }
  .back-brand__mark { width: 110px; height: 110px; background: var(--gold); }
  .back-brand__name { color: var(--gold); font-weight: 700; font-size: 40px; letter-spacing: 0.02em; }
  .back-web {
    position: absolute; left: 0; right: 0; top: 378px; text-align: center;
    color: var(--gold); font-size: 20px; letter-spacing: 0.6em;
  }
</style>
</head>
<body>

<section class="card card--front">
  <div class="brand">
    <span class="brand__mark"></span>
    <span class="brand__name">Stoneway Real Estate</span>
  </div>

  <div class="divider"></div>

  <div class="info">
    <p class="info__name">DANIEL REYES</p>
    <p class="info__title">CEO/FOUNDER</p>
    <p class="info__address">4120 Juniper Court<br>Fairbanks, Alaska 99701</p>
    <ul class="contacts">
      <li>
        <svg viewBox="0 0 24 24" aria-hidden="true"><path d="M6.6 10.8a15.1 15.1 0 0 0 6.6 6.6l2.2-2.2a1 1 0 0 1 1-.25 11.4 11.4 0 0 0 3.6.57 1 1 0 0 1 1 1V20a1 1 0 0 1-1 1A17 17 0 0 1 3 4a1 1 0 0 1 1-1h3.5a1 1 0 0 1 1 1c0 1.25.2 2.45.57 3.57a1 1 0 0 1-.25 1z"/></svg>
        555 210 3478
      </li>
      <li>
        <svg viewBox="0 0 24 24" aria-hidden="true"><path d="M7 1h10a2 2 0 0 1 2 2v18a2 2 0 0 1-2 2H7a2 2 0 0 1-2-2V3a2 2 0 0 1 2-2zm0 3v15h10V4z"/></svg>
        555 318 6642
      </li>
      <li>
        <svg viewBox="0 0 24 24" aria-hidden="true"><path d="M6 2h12v6H6zM3 9h18a2 2 0 0 1 2 2v7h-4v4H5v-4H1v-7a2 2 0 0 1 2-2zm4 8v3h10v-3z"/></svg>
        555 407 1925
      </li>
      <li>
        <svg viewBox="0 0 24 24" aria-hidden="true"><path d="M2 5h20v14H2zm2 2v.5l8 5 8-5V7l-8 5z"/></svg>
        daniel@stonewayre.com
      </li>
      <li>
        <svg viewBox="0 0 24 24" aria-hidden="true"><path d="M12 2a10 10 0 1 0 0 20 10 10 0 0 0 0-20zm-1 17.9A8 8 0 0 1 4 12l5 5v1a2 2 0 0 0 2 2zm6.9-2.5A2 2 0 0 0 16 16h-1v-3a1 1 0 0 0-1-1H8v-2h2a1 1 0 0 0 1-1V7h2a2 2 0 0 0 2-2v-.4a8 8 0 0 1 2.9 12.8z"/></svg>
        www.stonewayre.com
      </li>
    </ul>
  </div>
</section>

<section class="card card--back">
  <span class="social-square"></span>
  <div class="back-brand">
    <span class="back-brand__mark"></span>
    <span class="back-brand__name">Stoneway Real Estate</span>
  </div>
  <p class="back-web">www.stonewayre.com</p>
</section>

</body>
</html>
```